2018 Desk Calendar Design with Better Spine, Better Health with Chiropractic

In conjunction with the Federation of Spinal Wellness Malaysia (FSW), we are organizing a 2018 desk calendar design. The cover page and monthly design size is 210mm (H) x 195mm (W). The will be a total of 27 designs including a cover page (front) [Sample 1], cover page (back) Malaysia National & States Holiday 2018 (https://restdaylist.example.my/2018-dates/) [Sample 2], 12 months design (front) [Sample 3 and 4], 12 months design (back) [Sample 5], Last page (2017 and 2019 calendar) [Sample 6].

Below are some recommendations for monthly back cover design. The main theme remain as Better SPINE, Better HEALTH with CHIROPRACTIC. Each month can in collaborate with of the following element:-

Suggestion 1 (Celebration of the Month)
January - New Year
February - Chinese New Year
March -
April -
May - Labour Day
June - Aidilfitri Festival
July-
August - Independent Day
September - Malaysia Day
October - World Spine Day
November - Deepavali Festival
December - Christmas

Suggestion 2 (States in Malaysia)
January - Perlis
February - Kedah
March - Penang
April - Perak
May - Selangor
June - Negeri Sembilan
July- Melaka
August - Johor
September - Pahang
October - Terengganu
November - Kelantan
December - Sabah & Sarawak

Target Market(s)

Chiropractors and Public

Industry/Entity Type

Chiropractor

Colors

Designer to choose colors to be used in the design.

Requirements
Must have
• The theme for the desk calendar design is Better Spine, Better Health with Chiropractic.
• The cover page should include 5th Anniversary element.
Nice to have
• Lunar or Islamic calendar is optional in the Gregorian calendar.
• AI Format
• Footnote of each page www.spinefsw.example.org

```html
<!DOCTYPE html>
<html lang="en">
<head>
<meta charset="utf-8">
<title>Better Spine Better Health – 2018 Calendar Cover</title>
<link href="https://fonts.googleapis.com/css2?family=Arimo:wght@400;700&display=swap" rel="stylesheet">
<style>
  :root {
    --violet: #5253a6;
    --yellow: #f7e31a;
    --white: #ffffff;
    --ink: #111111;
    --photo-light: #f4f2ee;
    --photo-warm: #e7c9b4;
    --photo-green: #9fc06a;
    --photo-room: #d9dde2;
    --photo-shirt: #5aa4d6;
  }
  html, body { margin: 0; padding: 0; overflow: hidden; background: var(--white); }
  .cover {
    position: relative; width: 1200px; height: 1115px; overflow: hidden;
    background: var(--white); font-family: "Arimo", Arial, sans-serif; font-weight: 700;
  }
  .photo { position: absolute; }
  .photo--healthy-living {
    left: 440px; top: 50px; width: 760px; height: 690px;
    background: radial-gradient(ellipse at 60% 35%, var(--photo-warm) 0%, var(--photo-light) 45%),
                linear-gradient(to bottom, var(--photo-light) 65%, var(--photo-green) 100%);
    background-blend-mode: multiply;
  }
  .photo--adjustment {
    left: 0; top: 740px; width: 1200px; height: 375px;
    background: radial-gradient(ellipse at 62% 55%, var(--photo-shirt) 0%, var(--photo-room) 48%, var(--photo-light) 100%);
  }
  .binding { position: absolute; left: 195px; top: 24px; display: flex; gap: 16px; }
  .binding span { width: 24px; height: 24px; background: var(--ink); display: block; }
  .swoosh { position: absolute; left: 0; top: 0; }
  .headline { position: absolute; left: 80px; top: 72px; color: var(--yellow); line-height: 1; }
  .headline__line { display: block; font-size: 50px; letter-spacing: -0.5px; white-space: nowrap; }
  .headline__line--spine { margin-left: 0; }
  .headline__line--health { margin-left: 40px; margin-top: 10px; }
  .headline__line--with { margin-left: 40px; margin-top: 20px; }
  .rule { position: absolute; height: 4px; background: var(--white); }
  .rule--health { left: 100px; top: 205px; width: 205px; }
  .rule--year { left: 210px; top: 412px; width: 245px; }
  .rule--anniversary { left: 160px; top: 1005px; width: 195px; }
  .year { position: absolute; left: 210px; top: 312px; color: var(--white); font-size: 100px; line-height: 1; letter-spacing: 1px; }
  .year-label { position: absolute; left: 228px; top: 420px; color: var(--yellow); font-size: 54px; font-weight: 400; }
  .org-mark { position: absolute; left: 240px; top: 528px; display: flex; align-items: center; gap: 12px; color: var(--yellow); font-size: 48px; }
  .org-mark__dot { width: 26px; height: 26px; border-radius: 50%; background: var(--yellow); }
  .anniversary { position: absolute; left: 24px; top: 836px; color: var(--yellow); }
  .anniversary__number { position: absolute; left: 0; top: 0; font-size: 170px; line-height: 1; }
  .anniversary__suffix { position: absolute; left: 128px; top: 10px; font-size: 62px; }
  .anniversary__text { position: absolute; left: 136px; top: 92px; font-size: 38px; line-height: 1.2; white-space: nowrap; }
  .web-address { position: absolute; left: 28px; top: 1030px; color: var(--white); font-size: 46px; letter-spacing: -0.5px; white-space: nowrap; }
</style>
</head>
<body>
<main class="cover">
  <div class="photo photo--healthy-living" role="img" aria-label="Photo of a smiling woman in sportswear holding a glass of orange juice, with fresh fruit and vegetables"></div>
  <div class="photo photo--adjustment" role="img" aria-label="Photo of a chiropractor adjusting the lower back of a patient lying on a treatment table"></div>

  <svg class="swoosh" width="1200" height="1115" viewBox="0 0 1200 1115" aria-hidden="true">
    <path fill="var(--violet)" d="M0,0 L742,0 C605,242 504,484 468,696 C383,605 161,464 0,353 Z"/>
    <path fill="var(--violet)" d="M0,908 C161,868 262,807 323,756 C383,908 464,1008 565,1115 L0,1115 Z"/>
  </svg>

  <div class="binding" aria-hidden="true">
    <span></span><span></span><span></span><span></span><span></span><span></span><span></span>
    <span></span><span></span><span></span><span></span><span></span><span></span><span></span>
    <span></span><span></span><span></span><span></span><span></span><span></span><span></span>
    <span></span><span></span><span></span><span></span>
  </div>

  <h1 class="headline">
    <span class="headline__line headline__line--spine">Better SPINE</span>
    <span class="headline__line headline__line--health">Better HEALTH</span>
    <span class="headline__line headline__line--with">with CHIROPRACTIC</span>
  </h1>
  <div class="rule rule--health"></div>

  <div class="year">2018</div>
  <div class="rule rule--year"></div>
  <div class="year-label">Calendar</div>

  <div class="org-mark"><span class="org-mark__dot"></span>FSW</div>

  <div class="anniversary">
    <span class="anniversary__number">5</span>
    <span class="anniversary__suffix">th</span>
    <span class="anniversary__text">Celebrating<br>Anniversary</span>
  </div>
  <div class="rule rule--anniversary"></div>

  <div class="web-address">www.spinefsw.example.org</div>
</main>
</body>
</html>
```